Modern Business Card for Larkwell 2018

Our company assumes the best about people. We are creating an online community of entrepreneurs and business leaders who struggle with marketing their business online.

This business card should POP! We recently got a new logo and are launching a new website next month, so our business cards should make a statement that feels:
-Fresh
-Smart
-Trustworthy
-Fun

Target Market(s)

small business owners, entrepreneurs

Industry/Entity Type

Digital Marketing

Contact Information for Business Card

Dimensions: 3.5" x 2"

Font styles to use
Sans Serif

Colors
f37122
ffffff

Requirements
Must have
• We need a business card with a modern, bold design. We will use one side of the card as a lead-generation offer, so text on one side will need to fit up to 140 characters. The business card should stick to our core colors (orange, black, and white).
Nice to have
• We think a vertical "portrait" design could be interesting.
Should not have
• Should not look like a traditional business card. The round icon should stand out from a distance.

```html
<!DOCTYPE html>
<html lang="en">
<head>
<meta charset="utf-8">
<title>Larkwell Business Card</title>
<link rel="stylesheet" href="https://fonts.googleapis.com/css2?family=Oswald:wght@500&family=Work+Sans:wght@400;500;700&display=swap">
<style>
  :root {
    --stage: #1c1c1d;
    --card: #232324;
    --card-edge: #2c2c2d;
    --orange: #f37122;
    --white: #ffffff;
    --silver: #d4d4d6;
    --muted: #e6e6e6;
  }
  * { margin: 0; padding: 0; box-sizing: border-box; }
  html, body { width: 1200px; height: 900px; overflow: hidden; background: var(--stage); }
  body { font-family: "Work Sans", sans-serif; color: var(--white); position: relative; }

  .card {
    position: absolute;
    left: 320px;
    width: 560px;
    height: 320px;
    background: linear-gradient(135deg, var(--card-edge), var(--card));
  }
  .card--front { top: 70px; }
  .card--back { top: 470px; }

  /* Front: brand + offer */
  .brand {
    position: absolute;
    top: 58px; left: 0; right: 0;
    display: flex; flex-direction: column; align-items: center; gap: 10px;
  }
  .brand__dot {
    width: 44px; height: 44px; border-radius: 50%;
    background: var(--silver);
  }
  .brand__name {
    font-weight: 700; font-size: 58px; letter-spacing: 2px;
    color: var(--silver); line-height: 1;
  }
  .offer {
    position: absolute; top: 190px; left: 0; right: 0;
    text-align: center; font-size: 12px; line-height: 1.35; color: var(--muted);
  }
  .rule {
    position: absolute; top: 232px; left: 60px; right: 60px;
    height: 1px; background: var(--orange); opacity: .6;
  }
  .tagline {
    position: absolute; top: 244px; left: 0; right: 0;
    text-align: center; font-size: 15px; letter-spacing: .5px; color: var(--white);
  }

  /* Back: person + contacts */
  .person {
    position: absolute; top: 110px; left: 60px; width: 230px; text-align: right;
  }
  .person__name {
    font-family: "Oswald", sans-serif; font-weight: 500; font-size: 38px;
    color: var(--orange); letter-spacing: 1px; line-height: 1.05;
  }
  .person__role { font-size: 16px; letter-spacing: .5px; margin-top: 4px; }
  .divider {
    position: absolute; top: 115px; left: 312px; width: 2px; height: 58px; background: var(--white);
  }
  .contacts {
    position: absolute; top: 112px; left: 332px;
    list-style: none; font-size: 16px; line-height: 22px; letter-spacing: .3px;
  }
  .contacts li { display: flex; align-items: center; gap: 8px; }
  .contacts svg { width: 11px; height: 11px; flex: none; }
  .accent { color: var(--orange); }
  .address {
    position: absolute; bottom: 48px; left: 0; right: 0;
    text-align: center; font-size: 17px; letter-spacing: .5px;
  }
</style>
</head>
<body>
  <section class="card card--front">
    <div class="brand">
      <span class="brand__dot"></span>
      <span class="brand__name">LARKWELL</span>
    </div>
    <p class="offer">Get your free Larkwell<br>Starter Package and our marketing guide today at</p>
    <div class="rule"></div>
    <p class="tagline">REACH MORE PEOPLE. MAKE MORE MONEY. CREATE MORE IMPACT.</p>
  </section>

  <section class="card card--back">
    <div class="person">
      <h1 class="person__name">DANA WHITFIELD</h1>
      <p class="person__role">Story Marketing Coach</p>
    </div>
    <div class="divider"></div>
    <ul class="contacts">
      <li>
        <svg viewBox="0 0 12 12" aria-hidden="true"><path d="M2.5 1 L4.5 1 L5.2 3.6 L4 4.6 C4.7 6 6 7.3 7.4 8 L8.4 6.8 L11 7.5 L11 9.5 C11 10.3 10.3 11 9.5 11 C5 11 1 7 1 2.5 C1 1.7 1.7 1 2.5 1 Z" fill="#f37122"/></svg>
        (555) 014-2278
      </li>
      <li>
        <svg viewBox="0 0 12 12" aria-hidden="true"><rect x="1" y="2.5" width="10" height="7" fill="none" stroke="#f37122" stroke-width="1.2"/><path d="M1 2.5 L6 6.5 L11 2.5" fill="none" stroke="#f37122" stroke-width="1.2"/></svg>
        dana@larkwellnow.com
      </li>
      <li>
        <svg viewBox="0 0 12 12" aria-hidden="true"><circle cx="6" cy="6" r="5" fill="none" stroke="#f37122" stroke-width="1.1"/><ellipse cx="6" cy="6" rx="2.2" ry="5" fill="none" stroke="#f37122" stroke-width="1"/><path d="M1 6 H11" stroke="#f37122" stroke-width="1"/></svg>
        <span>www.<span class="accent">larkwellnow</span>.com</span>
      </li>
    </ul>
    <p class="address">AZ2000 , 45/8M. Korvelin Lane Norden city, Westmark</p>
  </section>
</body>
</html>
```